Interior design service, along with home organization, packing, and staging, home and business. As well as staging in conjunction with real estate sales.
Updates

Love many of your designs and will be choosing today. To inform you of the exact details needed, the name of the company is "Flourish by Marnie T" , my phone number and e-,ail need to be included. i also need either description or some sort of bullet points that give an idea of the following:

- Interior design for home and business
- Home organization and packing
- Staging for personal and professional space
- Real estate stagingĀ 

Thank you

Target Market(s)

wide audience, but most importantly people looking for a quality service

Industry/Entity Type

Real Estate

Contact Information for Business Card

Flourish By Marnie T
Marnie Tolvery
(555)687-3914
mtbrisco@postwell.example

Requirements
Must have
• I'm 29 so i want my card to reflect something professional but still fresh. I don't have any specific photos or quotes that Ive included, however I like the card to reflect a personal touch, which is what I'm seeking from this service in the design of my card. Thanks!

```html
<!DOCTYPE html>
<html lang="en">
<head>
<meta charset="utf-8">
<title>Flourish By Marnie T — Business Card</title>
<link href="https://fonts.googleapis.com/css2?family=Marcellus&family=Federo&display=swap" rel="stylesheet">
<style>
  :root {
    --backdrop: #5c5c5e;
    --front-deep: #3f78c4;
    --front-light: #6cbde0;
    --front-band: #4a82c8;
    --front-frame: #ffffff;
    --back-base: #0b0d0f;
    --back-tile: #2b3035;
    --back-frame: #59c6ee;
    --name-cyan: #3fa9e6;
    --label-blue: #4a8fd8;
    --divider-blue: #3a8fd6;
    --white: #ffffff;
  }
  * { margin: 0; padding: 0; box-sizing: border-box; }
  html, body { width: 1200px; height: 960px; overflow: hidden; }
  body { background: var(--backdrop); position: relative; }

  .card { position: absolute; overflow: hidden; }

  /* Front side */
  .card-front {
    left: 187px; top: 38px; width: 600px; height: 353px;
  }
  .front-mosaic {
    position: absolute; inset: 0;
    background: linear-gradient(100deg, var(--front-deep) 0%, #569fd6 55%, var(--front-light) 100%);
  }
  .front-band { position: absolute; left: 0; background: var(--front-band); opacity: .9; }
  .front-band--upper { top: 36px; height: 34px; width: 566px; }
  .front-band--lower { top: 235px; height: 32px; width: 100%; }
  .front-frame {
    position: absolute; inset: 8px;
    border: 1.5px solid var(--front-frame);
  }
  .front-question {
    position: absolute; color: var(--white);
    font-family: "Marcellus", serif; white-space: nowrap;
  }
  .front-question--lead { left: 41px; top: 104px; font-size: 43px; }
  .front-question--key { left: 60px; top: 164px; font-size: 62px; }
  .service-list {
    position: absolute; left: 20px; right: 20px; top: 280px;
    list-style: none; text-align: center;
    font-family: "Marcellus", serif; font-size: 17px; line-height: 25px;
    color: var(--white);
  }

  /* Back side */
  .card-back {
    left: 470px; top: 432px; width: 597px; height: 349px;
  }
  .back-mosaic {
    position: absolute; inset: 0;
    background:
      radial-gradient(ellipse at 85% 30%, var(--back-tile) 0%, transparent 55%),
      radial-gradient(ellipse at 15% 85%, var(--back-tile) 0%, transparent 50%),
      var(--back-base);
  }
  .back-frame {
    position: absolute; inset: 8px;
    border: 1.5px solid var(--back-frame);
  }
  .back-text {
    position: absolute; font-family: "Federo", sans-serif; white-space: nowrap;
  }
  .company-tag { left: 54px; top: 40px; font-size: 15px; color: var(--name-cyan); }
  .company-name { left: 92px; top: 60px; font-size: 38px; color: var(--name-cyan); }
  .contact-label { font-size: 24px; color: var(--label-blue); }
  .contact-value { font-size: 22px; color: var(--label-blue); }
  .name-label { right: 321px; top: 188px; }
  .name-value { right: 321px; top: 218px; font-size: 20px; color: var(--name-cyan); }
  .phone-label { left: 311px; top: 152px; }
  .phone-value { left: 311px; top: 186px; }
  .email-label { left: 311px; top: 230px; font-size: 26px; }
  .email-value { left: 311px; top: 266px; font-size: 18px; color: var(--name-cyan); }
  .contact-divider { position: absolute; left: 295px; top: 144px; }
</style>
</head>
<body>

  <section class="card card-front" aria-label="Card front">
    <div class="front-mosaic" role="img" aria-label="Blue mosaic of soft square tiles"></div>
    <div class="front-band front-band--upper"></div>
    <div class="front-band front-band--lower"></div>
    <div class="front-frame"></div>
    <p class="front-question front-question--lead">Are you looking for a</p>
    <p class="front-question front-question--key">quality service??</p>
    <ul class="service-list">
      <li>Interior Design for Home &amp; Business · Organization &amp; Packing</li>
      <li>Personal &amp; Professional Staging · Real Estate Staging</li>
    </ul>
  </section>

  <section class="card card-back" aria-label="Card back">
    <div class="back-mosaic" role="img" aria-label="Dark charcoal mosaic of square tiles"></div>
    <div class="back-frame"></div>
    <p class="back-text company-tag">Flourish By,</p>
    <p class="back-text company-name">Marnie T</p>

    <p class="back-text contact-label name-label">Name</p>
    <p class="back-text name-value">Marnie Tolvery</p>

    <svg class="contact-divider" width="4" height="144" viewBox="0 0 4 144" aria-hidden="true">
      <rect width="4" height="144" fill="var(--divider-blue)"/>
    </svg>

    <p class="back-text contact-label phone-label">Phone</p>
    <p class="back-text contact-value phone-value">(555)687-3914</p>
    <p class="back-text contact-label email-label">Email</p>
    <p class="back-text email-value">mtbrisco@postwell.example</p>
  </section>

</body>
</html>
```